BuildLinkHub.com Full Stationery Design

Business Card will have all info on it. Letterhead will not have name, title or mobile number. Keep general feeling very clean, using colors from the logo as accents.
Name:Dale Marchetti
Title:President
Phone: 1-800-555-0142
Cell: 306-555-0187
email: dale@buildlinkhub.example
website: www.buildlinkhub.example
Address:
PO Box 947
Carrow Creek, AB
S0J2T0

Target Market(s)

Construction Business owners

Industry/Entity Type

Business

Contact Information for Business Card

Name:Dale Marchetti
Title:President
Phone: 1-800-555-0142
Cell: 306-555-0187
Address:
PO Box 947
Carrow Creek, AB
S0J2T0

Font styles to use
Sans Serif

Requirements
Must have
• Clean look
Should not have
• Images or cartoon type characters or tools

```html
<!DOCTYPE html>
<html lang="en">
<head>
<meta charset="utf-8">
<title>BuildLinkHub.com Letterhead</title>
<link href="https://fonts.googleapis.com/css2?family=Montserrat:wght@500;700&display=swap" rel="stylesheet">
<style>
  :root {
    --backdrop: #efd3cf;
    --paper: #ffffff;
    --ink: #4a5563;
    --ink-soft: #7a828c;
    --accent: #f0501e;
    --accent-deep: #d9261c;
    --accent-warm: #f7801e;
  }
  * { margin: 0; padding: 0; box-sizing: border-box; }
  html, body {
    width: 1200px; height: 784px; overflow: hidden;
    background: var(--backdrop);
    font-family: "Montserrat", Arial, sans-serif;
  }
  .letterhead {
    position: absolute;
    left: 311px; top: 22px;
    width: 578px; height: 740px;
    background: var(--paper);
    box-shadow: 0 6px 18px rgba(120, 60, 60, 0.18);
    overflow: hidden;
  }
  .corner-accent {
    position: absolute; left: 0; top: 0;
    width: 200px; height: 70px;
  }
  .brand {
    position: absolute; left: 40px; top: 78px;
    display: flex; align-items: center; gap: 10px;
  }
  .brand-square {
    width: 22px; height: 22px;
    background: var(--accent);
  }
  .brand-name {
    font-size: 22px; font-weight: 700;
    color: var(--ink);
    letter-spacing: -0.2px;
  }
  .contact {
    position: absolute; right: 40px; top: 80px;
    list-style: none;
    font-size: 8.5px; font-weight: 500;
    color: var(--ink-soft);
    line-height: 1.55;
  }
  .contact li { display: flex; align-items: center; gap: 6px; white-space: nowrap; }
  .contact-icon { width: 9px; height: 9px; flex: none; }
</style>
</head>
<body>
  <main class="letterhead">
    <svg class="corner-accent" viewBox="0 0 200 70" aria-hidden="true">
      <defs>
        <linearGradient id="cornerFill" x1="0" y1="0" x2="1" y2="0">
          <stop offset="0" stop-color="#f7801e"/>
          <stop offset="1" stop-color="#d9261c"/>
        </linearGradient>
      </defs>
      <polygon points="0,0 200,0 0,70" fill="url(#cornerFill)"/>
      <polygon points="0,14 170,0 200,0 0,70" fill="#ffffff" opacity="0"/>
    </svg>

    <div class="brand">
      <span class="brand-square"></span>
      <span class="brand-name">BuildLinkHub.com</span>
    </div>

    <ul class="contact">
      <li>
        <svg class="contact-icon" viewBox="0 0 10 10" aria-hidden="true"><circle cx="5" cy="5" r="5" fill="#f0501e"/><path d="M5 2.2a1.9 1.9 0 0 0-1.9 1.9C3.1 5.6 5 7.8 5 7.8s1.9-2.2 1.9-3.7A1.9 1.9 0 0 0 5 2.2z" fill="#fff"/></svg>
        PO Box 947, Carrow Creek, AB S0J2T0
      </li>
      <li>
        <svg class="contact-icon" viewBox="0 0 10 10" aria-hidden="true"><circle cx="5" cy="5" r="5" fill="#f0501e"/><path d="M3.3 2.5l1 1-.5.7c.3.7.8 1.2 1.5 1.5l.7-.5 1 1-.6.8C4.9 7 3 5.1 2.5 3.1z" fill="#fff"/></svg>
        Phone: 1-800-555-0142
      </li>
      <li>
        <svg class="contact-icon" viewBox="0 0 10 10" aria-hidden="true"><circle cx="5" cy="5" r="5" fill="#f0501e"/><rect x="2.5" y="3.2" width="5" height="3.6" fill="#fff"/><path d="M2.5 3.2L5 5.2 7.5 3.2" stroke="#f0501e" stroke-width="0.6" fill="none"/></svg>
        dale@buildlinkhub.example
      </li>
      <li>
        <svg class="contact-icon" viewBox="0 0 10 10" aria-hidden="true"><circle cx="5" cy="5" r="5" fill="#f0501e"/><circle cx="5" cy="5" r="2.6" stroke="#fff" stroke-width="0.7" fill="none"/><path d="M2.4 5h5.2M5 2.4v5.2" stroke="#fff" stroke-width="0.6"/></svg>
        www.buildlinkhub.example
      </li>
    </ul>
  </main>
</body>
</html>
```